African homeware retailer needs a web page design

We need a web page design for a new homeware and accessories store based in Johannesburg, South Africa. Our store carries modern African inspired items from designers that support social development and poverty alleviation initiatives. We have a particular preference for outfits that are centred on the empowerment of women.

Our business celebrates the skill, design and product of African craft and the work of designers looking to take that forward in a socially beneficial way (creating employment, developing skills, supporting local crafts people etc). We aim to carry items and inspirations from all over the African continent.

We would like to see a design that communicates African beauty and elegance without the typical tribal references that are made in reference to African craft or art.

We would like the web page to be stylish, uncomplicated, modern, captivating and appealing to the discerning customer. A similar value proposition is that of http://www.marlowtenwick.example/.

This is an e-commerce website which must be attractive to both individual buyers and design professionals so the website needs to look professional.

Here are links to some websites we like:
http://www.quenbyhollis.example/
http://www.dravelo.example/

Our logo is attached to the brief.

Target Market(s)

Our target market is female, age 20-50. However should not alienate the design conscious male customer therefore

Industry/Entity Type

E-Commerce

Requirements
Must have
• - A featured product banner which includes a photograph and text. This should be easy to edit as we will be changing the featured product regularly
- An easily expendable products section with categories. Examples of categories could be cushions, bedding, crockery etc. Should be easy to add new categories as well as new product pictures
- Home/landing page should be uncluttered
- Should use the logo and should be easy to change the logo which we have in various colour combinations. We plan to change the logo colours depending on circumstance e.g. make it red and white around Valentines day (similar to the way Vintrel frequently changes the logo on their landing page)

```html
<!DOCTYPE html>
<html lang="en">
<head>
<meta charset="utf-8">
<title>Tandeka Home — homeware &amp; accessories</title>
<link rel="stylesheet" href="https://fonts.googleapis.com/css2?family=Lato:wght@300;400&family=Noto+Serif&family=Josefin+Sans:wght@400&display=swap">
<style>
  :root {
    --cream: #fbf6dc;
    --cream-glow: #fdfaea;
    --ink: #3a3733;
    --muted: #6a6660;
    --teal: #1b7574;
    --orange: #e0531f;
    --brown: #5a3526;
    --green: #0a9a1a;
    --blue: #0a6aa0;
    --teal-tile: #0e7878;
    --orange-tile: #e6501f;
    --brown-tile: #573324;
    --purple: #6a3296;
  }
  * { box-sizing: border-box; margin: 0; padding: 0; }
  html, body { width: 1200px; height: 797px; overflow: hidden; }
  body {
    position: relative;
    background: radial-gradient(circle at 810px 390px, var(--cream-glow) 0, var(--cream-glow) 330px, var(--cream) 360px);
    font-family: "Lato", sans-serif;
    color: var(--ink);
  }
  .phone {
    position: absolute; top: 17px; right: 134px;
    display: flex; align-items: center; gap: 4px;
    font-size: 14px; letter-spacing: .6px; color: var(--muted);
  }
  .brand { position: absolute; left: 134px; top: 20px; width: 296px; text-align: center; }
  .brand-mark {
    width: 156px; height: 156px; margin: 10px auto 40px;
    background: var(--orange); border-radius: 6px;
  }
  .brand-name {
    font-family: "Josefin Sans", sans-serif; font-weight: 400;
    font-size: 40px; letter-spacing: 3px; color: var(--orange); line-height: 1;
  }
  .brand-tag { margin-top: 12px; font-family: "Noto Serif", serif; font-size: 13px; letter-spacing: 1px; color: var(--brown); }
  .statement {
    position: absolute; left: 134px; top: 524px; width: 500px;
    font-weight: 300; font-size: 28px; line-height: 35px; color: var(--ink);
  }
  .statement .accent-teal { color: var(--teal); }
  .statement .accent-orange { color: var(--orange); }
  .tiles { position: absolute; inset: 0; list-style: none; }
  .tile {
    position: absolute; width: 226px; height: 226px;
    display: flex; align-items: center; justify-content: center;
    text-align: center; text-decoration: none;
    font-family: "Noto Serif", serif; font-size: 23px; line-height: 27px;
    color: #fff; text-shadow: 0 1px 3px rgba(0,0,0,.45);
  }
  .tile .shape {
    position: absolute; left: 33px; top: 33px; width: 160px; height: 160px;
    transform: rotate(45deg); border-radius: 9px;
  }
  .tile .label { position: relative; }
  .tile--employment .shape { background: var(--green); }
  .tile--about .shape { background: var(--blue); }
  .tile--skills .shape { background: var(--orange-tile); }
  .tile--crafts .shape { background: var(--teal-tile); }
  .tile--shop .shape { background: var(--brown-tile); }
  .tile--enter .shape { background: var(--purple); }
  .tile--cushions .shape { background: linear-gradient(135deg, #b98a6a, #8a2a22 55%, #c23a2e); }
  .tile--bedding .shape { background: linear-gradient(135deg, #c8763a, #8c3a1e 50%, #d68a3c); }
  .tile--crockery .shape { background: linear-gradient(135deg, #a8541c, #3e2414 50%, #c9782a); }
  .footer-note { position: absolute; left: 134px; top: 760px; font-size: 14px; color: var(--ink); }
  .social { position: absolute; right: 134px; top: 762px; display: flex; gap: 8px; }
  .social span { width: 13px; height: 13px; border-radius: 50%; background: var(--muted); }
</style>
</head>
<body>
  <div class="phone">
    <svg width="12" height="16" viewBox="0 0 12 16" aria-hidden="true"><path d="M3 1 L5 1 L6 5 L4 6 Q5 10 8 12 L9 10 L12 12 L11 15 Q2 14 1 3 Z" fill="#6a6660"/></svg>
    0123-4477-09
  </div>

  <header class="brand">
    <div class="brand-mark"></div>
    <div class="brand-name">TANDEKA HOME</div>
    <div class="brand-tag">homeware &amp; accessories</div>
  </header>

  <p class="statement">We Have A <span class="accent-teal">Particular Preference</span> For Outfits That Are Centred On The <span class="accent-orange">Empowerment Of Women.</span></p>

  <nav>
    <ul class="tiles">
      <li><a class="tile tile--employment" href="#" style="left:430px;top:17px"><span class="shape"></span><span class="label">Creating<br>Employment</span></a></li>
      <li><a class="tile tile--about" href="#" style="left:692px;top:17px"><span class="shape"></span><span class="label">About</span></a></li>
      <li><a class="tile tile--cushions" href="#" style="left:561px;top:149px"><span class="shape" role="img" aria-label="Photograph of stacked woven cushions in red and brown"></span><span class="label">Cushions</span></a></li>
      <li><a class="tile tile--bedding" href="#" style="left:824px;top:149px"><span class="shape" role="img" aria-label="Photograph of folded patterned textiles in orange tones"></span><span class="label">Bedding</span></a></li>
      <li><a class="tile tile--skills" href="#" style="left:430px;top:280px"><span class="shape"></span><span class="label">Developing<br>Skills</span></a></li>
      <li><a class="tile tile--crafts" href="#" style="left:692px;top:280px"><span class="shape"></span><span class="label">Supporting<br>Local<br>Crafts People</span></a></li>
      <li><a class="tile tile--shop" href="#" style="left:561px;top:411px"><span class="shape"></span><span class="label">Shop Now!</span></a></li>
      <li><a class="tile tile--crockery" href="#" style="left:824px;top:411px"><span class="shape" role="img" aria-label="Photograph of painted ceramic bowls and pots"></span><span class="label">Crockery</span></a></li>
      <li><a class="tile tile--enter" href="#" style="left:692px;top:542px"><span class="shape"></span><span class="label">Enter<br>Site</span></a></li>
    </ul>
  </nav>

  <footer>
    <p class="footer-note">© 2014 TandekaHome. All rights reserved.</p>
    <div class="social" aria-label="Social links"><span></span><span></span><span></span><span></span><span></span></div>
  </footer>
</body>
</html>
```